Business card design for my company.
I would like the card's background colour to be black. You can also see our web site to get an idea of our brand. https://www.tmwhomecrafting.com.au/
- Name
- Email

```html
<!DOCTYPE html>
<html lang="en">
<head>
<meta charset="utf-8">
<title>TMW Home Crafting – Business Card</title>
<link rel="stylesheet" href="https://fonts.googleapis.com/css2?family=Montserrat:wght@400;500;700;800&display=swap">
<style>
  :root {
    --backdrop: #4b4b4b;
    --card: #141414;
    --green: #0b9444;
    --white: #f2f2f2;
    --grey-text: #bdbdbd;
  }
  * { box-sizing: border-box; margin: 0; padding: 0; }
  html, body {
    width: 1200px; height: 800px; overflow: hidden;
    background: var(--backdrop);
    font-family: "Montserrat", Arial, sans-serif;
  }
  .stage { position: relative; width: 1200px; height: 800px; }

  .card {
    position: absolute;
    background: var(--card);
    border-radius: 22px;
    border: 3px solid var(--green);
    box-shadow: 0 18px 40px rgba(0,0,0,.35);
  }

  /* Front: portrait */
  .card--front {
    left: 130px; top: 130px; width: 340px; height: 550px;
    display: flex; flex-direction: column; align-items: center;
    padding: 70px 30px 40px;
    color: var(--white);
    text-align: center;
  }
  .brand-name {
    display: flex; align-items: center; gap: 12px;
    font-weight: 800; font-size: 26px; letter-spacing: 2px;
    color: var(--white); line-height: 1.15;
  }
  .brand-name__mark { width: 22px; height: 22px; background: var(--green); flex: none; }
  .brand-name__text { text-align: left; }

  .person { margin-top: 70px; }
  .person__name { font-weight: 700; font-size: 27px; color: var(--green); }
  .person__role { font-size: 14px; letter-spacing: 1px; margin-top: 6px; }

  .divider { display: flex; align-items: center; gap: 8px; width: 100%; margin: 24px 0 16px; }
  .divider__line { flex: 1; height: 1.5px; background: var(--green); }
  .icon {
    width: 28px; height: 28px; border-radius: 7px; background: var(--green);
    display: flex; align-items: center; justify-content: center;
  }
  .icon svg { width: 18px; height: 18px; }

  .contact { list-style: none; font-size: 13.5px; line-height: 1.9; letter-spacing: .3px; }
  .rule { width: 100%; height: 1.5px; background: var(--green); margin: 18px 0 16px; }
  .address { font-size: 14px; letter-spacing: .3px; }

  /* Back: landscape */
  .card--back {
    left: 530px; top: 235px; width: 550px; height: 340px;
    display: flex; align-items: center; justify-content: center;
  }
  .back-brand {
    display: flex; align-items: center; gap: 18px;
    font-weight: 800; font-size: 40px; letter-spacing: 4px;
    color: var(--grey-text); line-height: 1.1;
  }
  .back-brand__mark { width: 34px; height: 34px; background: var(--grey-text); flex: none; }
</style>
</head>
<body>
<main class="stage">

  <section class="card card--front" aria-label="Business card front">
    <div class="brand-name">
      <span class="brand-name__mark"></span>
      <span class="brand-name__text">TMW<br>HOME CRAFTING</span>
    </div>

    <div class="person">
      <h1 class="person__name">Dan Whitfield</h1>
      <p class="person__role">General Manager</p>
    </div>

    <div class="divider">
      <span class="divider__line"></span>
      <span class="icon" aria-label="Phone">
        <svg viewBox="0 0 24 24" fill="#fff"><path d="M6.6 10.8a15.1 15.1 0 0 0 6.6 6.6l2.2-2.2c.3-.3.7-.4 1-.2 1.1.4 2.3.6 3.6.6.6 0 1 .4 1 1V20c0 .6-.4 1-1 1A17 17 0 0 1 3 4c0-.6.4-1 1-1h3.5c.6 0 1 .4 1 1 0 1.3.2 2.5.6 3.6.1.3 0 .7-.2 1z"/></svg>
      </span>
      <span class="icon" aria-label="Email">
        <svg viewBox="0 0 24 24" fill="none" stroke="#fff" stroke-width="2"><rect x="3" y="5" width="18" height="14" rx="1"/><path d="M3 6l9 7 9-7"/></svg>
      </span>
      <span class="icon" aria-label="Website">
        <svg viewBox="0 0 24 24" fill="none" stroke="#fff" stroke-width="1.8"><circle cx="12" cy="12" r="9"/><path d="M3 12h18M12 3c3 3 3 15 0 18M12 3c-3 3-3 15 0 18"/></svg>
      </span>
      <span class="divider__line"></span>
    </div>

    <ul class="contact">
      <li>0400 555 123</li>
      <li>info@tmwhomecrafting.com.au</li>
      <li>www.tmwhomecrafting.com.au</li>
    </ul>

    <div class="rule"></div>
    <p class="address">Kingsford, Tasmania, Australia</p>
  </section>

  <section class="card card--back" aria-label="Business card back">
    <div class="back-brand">
      <span class="back-brand__mark"></span>
      <span>TMW<br>HOME CRAFTING</span>
    </div>
  </section>

</main>
</body>
</html>
```